TA BRAMLEY BUSINESS CARD DESIGN PROJECT

We need to utilize our logo that was expertly created on PixelHarbor and now need to match this with a business card design.

```html
<!DOCTYPE html>
<html lang="en">
<head>
<meta charset="UTF-8">
<title>TA BRAMLEY Business Card</title>
<link rel="stylesheet" href="https://fonts.googleapis.com/css2?family=Poppins:wght@400;600;700&display=swap">
<style>
  :root {
    --brand-blue: #1157ac;
    --card-dark: #161616;
    --card-white: #ffffff;
    --stage: #d9d9db;
    --text-light: #f2f2f2;
  }
  * { margin: 0; padding: 0; box-sizing: border-box; }
  html, body { width: 1200px; height: 900px; overflow: hidden; }
  body {
    background: var(--stage);
    font-family: "Poppins", sans-serif;
    position: relative;
  }
  .card {
    position: absolute;
    left: 210px;
    width: 780px;
    height: 420px;
    border-radius: 26px;
    overflow: hidden;
    box-shadow: 0 6px 18px rgba(0,0,0,0.18);
  }
  .card--front { top: 20px; background: var(--brand-blue); }
  .card--back { top: 460px; background: var(--card-dark); }

  .brand-name {
    font-family: "Poppins", sans-serif;
    font-weight: 700;
    letter-spacing: 0.12em;
    white-space: nowrap;
  }
  .card--front .brand-name {
    position: absolute;
    left: 0; right: 0; top: 50%;
    transform: translateY(-50%);
    text-align: center;
    font-size: 70px;
    color: var(--card-white);
  }

  .back-curve { position: absolute; inset: 0; }

  .card--back .brand-name {
    position: absolute;
    left: 470px;
    width: 290px;
    top: 180px;
    text-align: center;
    font-size: 34px;
    color: var(--brand-blue);
  }

  .contact-block {
    position: absolute;
    left: 56px;
    top: 70px;
    color: var(--text-light);
  }
  .person-name {
    font-weight: 700;
    font-size: 30px;
    color: var(--brand-blue);
    line-height: 1.1;
    letter-spacing: -0.01em;
  }
  .person-role { font-size: 20px; margin-top: 2px; }
  .address {
    font-size: 18px;
    line-height: 1.45;
    margin-top: 46px;
    margin-left: 40px;
  }
  .contact-list {
    list-style: none;
    margin-top: 36px;
    margin-left: 40px;
    font-size: 18px;
    line-height: 1.55;
  }
  .contact-list li { display: flex; align-items: center; gap: 12px; }
  .contact-icon { width: 16px; height: 16px; flex: none; }
</style>
</head>
<body>
  <section class="card card--front" aria-label="Business card front">
    <p class="brand-name">TA BRAMLEY</p>
  </section>

  <section class="card card--back" aria-label="Business card back">
    <svg class="back-curve" viewBox="0 0 780 420" width="780" height="420" aria-hidden="true">
      <path d="M470 0 C400 120 430 300 610 420 L780 420 L780 0 Z" fill="#1157ac"/>
      <path d="M486 0 C420 120 450 300 640 420 L780 420 L780 0 Z" fill="#ffffff"/>
    </svg>

    <p class="brand-name">TA BRAMLEY</p>

    <div class="contact-block">
      <h1 class="person-name">DANIEL REED</h1>
      <p class="person-role">Director</p>
      <p class="address">2045 Lakeside, Orchard út<br>14-16. 2 floor 3.</p>
      <ul class="contact-list">
        <li>
          <svg class="contact-icon" viewBox="0 0 16 16" aria-hidden="true"><path d="M3 1.5l2.5 0 1 3.5-1.6 1.2c.8 1.7 2.2 3.1 3.9 3.9l1.2-1.6 3.5 1v2.5c0 .8-.7 1.5-1.5 1.5C6.6 13.5 2.5 9.4 1.5 3c0-.8.7-1.5 1.5-1.5z" fill="#1157ac"/></svg>
          +36 30 555 0142
        </li>
        <li>
          <svg class="contact-icon" viewBox="0 0 16 16" aria-hidden="true"><rect x="1" y="3" width="14" height="10" rx="1" fill="#1157ac"/><path d="M1.5 3.5l6.5 5 6.5-5" fill="none" stroke="#161616" stroke-width="1.3"/></svg>
          hello@brightmoor.hu
        </li>
        <li>
          <svg class="contact-icon" viewBox="0 0 16 16" aria-hidden="true"><circle cx="8" cy="8" r="7" fill="#1157ac"/><path d="M1 8h14M8 1c-3 3.5-3 10.5 0 14M8 1c3 3.5 3 10.5 0 14" fill="none" stroke="#161616" stroke-width="1"/></svg>
          www.brightmoor.hu
        </li>
      </ul>
    </div>
  </section>
</body>
</html>
```